Investment Management Firm Power point template

Marrow Holdings is a real estate investment firm focused on buying commercial office and residential property in the UK. We produce powerpoint presentations for our Board of Directors, Investment Committee and also to external investors.

We are looking for a powerpoint design template which we can use for future presentations which provide a professional look and feel.

Our current website: http://www.marrowholdings.example.co.uk/

Target Market(s)

Institution Investors, Board of Directors, Professionals

Industry/Entity Type

Real Estate

Requirements
Must have
• Leverage off the current logo and colour scheme. However, does not have to purely rely on this colour scheme.
• - Title page
• - Content Page
• - Slide where graphs can be incorporated
• - Slide where photos can be incorporated
• - Slide of UK Map which can show where the property portfolio is currently located
• - Other slides incorporating smart art or other designs that can be used for future presentations
Nice to have
• An example of graphics that we would love to have in the powerpoint pack which we can easily edit has been attached

```html
<!DOCTYPE html>
<html lang="en">
<head>
<meta charset="utf-8">
<title>Marrow Holdings – Graph Slide</title>
<link rel="stylesheet" href="https://fonts.googleapis.com/css2?family=Tenor+Sans&family=Open+Sans:wght@400;600;700&family=Oswald:wght@500;600&display=swap">
<style>
  :root {
    --page: #ffffff;
    --ink: #1e1e1e;
    --teal: #1a8c9c;
    --teal-deep: #2a5c68;
    --stage-a: #4e7c86;
    --stage-b: #2b5260;
    --stage-c: #6d9198;
    --red: #b8151f;
    --grey: #6b6b6b;
    --crane: #b9bfc2;
    --green: #4d9a3d;
    --orange: #cf6429;
    --gold: #c9952b;
    --crimson: #c0242a;
    --badge: #141414;
  }
  * { margin: 0; padding: 0; box-sizing: border-box; }
  html, body { width: 1200px; height: 1000px; overflow: hidden; background: var(--page); }
  .board { position: relative; width: 1200px; height: 1000px; }
  .board-title {
    position: absolute; top: 110px; left: 0; width: 1200px; text-align: center;
    font-family: "Tenor Sans", sans-serif; font-size: 30px; color: var(--ink);
  }
  .stage {
    position: absolute; left: 134px; top: 175px; width: 946px; height: 709px;
    background:
      radial-gradient(ellipse at 30% 70%, var(--stage-c) 0%, transparent 55%),
      radial-gradient(ellipse at 80% 20%, var(--stage-c) 0%, transparent 50%),
      linear-gradient(160deg, var(--stage-a), var(--stage-b));
    border: 1px solid #9fb3b8;
  }
  .stage-corner { position: absolute; left: 0; top: 0; width: 136px; height: 93px; background: var(--page); }
  .slide {
    position: absolute; left: 136px; top: 0; width: 770px; height: 627px;
    background: linear-gradient(180deg, #ffffff 0%, #f6f8f8 45%, #e6ecee 100%);
    box-shadow: 0 0 14px rgba(0,0,0,0.35);
  }
  .slide-fold { position: absolute; right: -2px; bottom: -10px; }
  .brand { position: absolute; left: 12px; top: 37px; display: flex; align-items: center; gap: 14px; }
  .brand-square { width: 52px; height: 55px; background: var(--teal-deep); }
  .brand-name {
    font-family: "Open Sans", sans-serif; font-weight: 600; font-size: 40px;
    color: #3a3a3a; letter-spacing: -0.5px;
  }
  .chart { position: absolute; left: 0; top: 0; }
  .heading { font-family: "Open Sans", sans-serif; fill: var(--red); }
  .label-red { font-family: "Oswald", sans-serif; font-weight: 600; fill: var(--red); font-size: 10px; letter-spacing: 0.3px; }
  .label-small { font-family: "Oswald", sans-serif; font-weight: 600; font-size: 9px; fill: var(--ink); }
  .axis { font-family: "Open Sans", sans-serif; font-size: 9px; fill: var(--ink); }
  .bar { fill: var(--teal); }
  .value { font-family: "Oswald", sans-serif; font-weight: 500; font-size: 13px; fill: var(--teal); }
  .market { font-family: "Oswald", sans-serif; font-weight: 600; font-size: 8.5px; fill: var(--ink); }
  .badge-title { font-family: "Oswald", sans-serif; font-weight: 500; font-size: 7.5px; fill: #ffffff; }
  .badge-pct { font-family: "Open Sans", sans-serif; font-size: 11px; fill: #8aa0a6; }
  .pound { font-family: "Tenor Sans", serif; font-size: 92px; font-weight: 700; }
</style>
</head>
<body>
<main class="board">
  <h1 class="board-title">Power point Graph Page</h1>

  <section class="stage">
    <div class="stage-corner"></div>
    <div class="slide">
      <div class="brand">
        <div class="brand-square"></div>
        <span class="brand-name">Marrow Holdings</span>
      </div>
      <svg class="slide-fold" width="48" height="58" viewBox="0 0 48 58" aria-hidden="true">
        <polygon points="48,0 48,58 0,58" fill="#1c1c1c"/>
      </svg>
    </div>

    <svg class="chart" width="946" height="709" viewBox="134 175 946 709">
      <text class="heading" x="383" y="332" font-size="25">Market snapshot</text>
      <text class="label-red" x="588" y="350">SPECULATIVE DEVELOPMENT – TOP 10 MARKETS</text>

      <text class="label-small" x="522" y="375">2%</text>
      <text class="label-small" x="680" y="375">% OF STOCK</text>
      <text class="label-small" x="868" y="375">5%</text>
      <line x1="520" y1="379" x2="888" y2="379" stroke="var(--teal)" stroke-width="1.5"/>
      <polygon points="888,375 896,379 888,383" fill="var(--teal)"/>

      <g role="img" aria-label="Tower crane silhouette carrying the bar chart">
        <rect x="355" y="393" width="550" height="15" fill="var(--crane)" opacity="0.55"/>
        <rect x="473" y="342" width="28" height="440" fill="var(--crane)" opacity="0.35"/>
      </g>

      <g stroke="var(--grey)" stroke-width="1">
        <line x1="538" y1="408" x2="538" y2="468"/><line x1="577" y1="408" x2="577" y2="468"/>
        <line x1="615" y1="408" x2="615" y2="468"/><line x1="653" y1="408" x2="653" y2="468"/>
        <line x1="692" y1="408" x2="692" y2="468"/><line x1="731" y1="408" x2="731" y2="468"/>
        <line x1="769" y1="408" x2="769" y2="468"/><line x1="808" y1="408" x2="808" y2="468"/>
        <line x1="847" y1="408" x2="847" y2="468"/><line x1="885" y1="408" x2="885" y2="468"/>
      </g>

      <text class="axis" x="430" y="471">0</text>
      <text class="axis" x="430" y="618">3</text>
      <text class="axis" x="395" y="547">m sq ft</text>
      <g stroke="var(--grey)" stroke-width="1">
        <line x1="440" y1="468" x2="520" y2="468"/>
        <line x1="440" y1="615" x2="935" y2="615"/>
        <line x1="440" y1="493" x2="446" y2="493"/><line x1="440" y1="518" x2="446" y2="518"/>
        <line x1="440" y1="543" x2="446" y2="543"/><line x1="440" y1="568" x2="446" y2="568"/>
        <line x1="440" y1="593" x2="446" y2="593"/>
      </g>

      <rect class="bar" x="522" y="468" width="32" height="24"/>
      <rect class="bar" x="561" y="468" width="32" height="20"/>
      <rect class="bar" x="600" y="468" width="30" height="44"/>
      <rect class="bar" x="637" y="468" width="32" height="15"/>
      <rect class="bar" x="676" y="468" width="32" height="11"/>
      <rect class="bar" x="715" y="468" width="32" height="15"/>
      <rect class="bar" x="753" y="468" width="32" height="127"/>
      <rect class="bar" x="792" y="468" width="33" height="152"/>
      <rect class="bar" x="831" y="468" width="32" height="20"/>
      <rect class="bar" x="869" y="468" width="32" height="11"/>

      <text class="value" x="522" y="506">0.5m</text>
      <text class="value" x="561" y="501">0.4m</text>
      <text class="value" x="598" y="527">0.9m</text>
      <text class="value" x="638" y="497">0.3m</text>
      <text class="value" x="677" y="493">0.2m</text>
      <text class="value" x="715" y="497">0.3m</text>
      <text class="value" x="753" y="607">2.3m</text>
      <text class="value" x="792" y="632">2.6m</text>
      <text class="value" x="831" y="501">0.4m</text>
      <text class="value" x="869" y="493">0.2m</text>

      <text class="market" transform="translate(536,512) rotate(90)">EDINBURGH</text>
      <text class="market" transform="translate(572,508) rotate(90)">GLASGOW</text>
      <text class="market" transform="translate(611,532) rotate(90)">MANCHESTER</text>
      <text class="market" transform="translate(650,503) rotate(90)">MIDTOWN</text>
      <text class="market" transform="translate(689,499) rotate(90)">UXBRIDGE</text>
      <text class="market" transform="translate(728,503) rotate(90)">CAMBRIDGE</text>
      <text class="market" transform="translate(766,613) rotate(90)">CITY</text>
      <text class="market" transform="translate(806,638) rotate(90)">WEST END</text>
      <text class="market" transform="translate(844,508) rotate(90)">READING</text>
      <text class="market" transform="translate(882,499) rotate(90)">STAINES</text>

      <text class="label-red" x="645" y="688" text-anchor="middle">2014 TOTAL RETURNS (% PA)</text>

      <g>
        <circle cx="443" cy="761" r="59" fill="var(--badge)"/>
        <text class="badge-title" x="443" y="721" text-anchor="middle">REST OF THE UK</text>
        <text class="pound" x="443" y="792" text-anchor="middle" fill="var(--green)">£</text>
        <text class="badge-pct" x="443" y="812" text-anchor="middle">16.9%</text>
      </g>
      <g>
        <circle cx="579" cy="761" r="59" fill="var(--badge)"/>
        <text class="badge-title" x="579" y="721" text-anchor="middle">CITY</text>
        <text class="pound" x="579" y="792" text-anchor="middle" fill="var(--orange)">£</text>
        <text class="badge-pct" x="579" y="812" text-anchor="middle">20.2%</text>
      </g>
      <g>
        <circle cx="715" cy="761" r="59" fill="var(--badge)"/>
        <text class="badge-title" x="715" y="721" text-anchor="middle">SOUTH EAST</text>
        <text class="pound" x="715" y="792" text-anchor="middle" fill="var(--gold)">£</text>
        <text class="badge-pct" x="715" y="812" text-anchor="middle">22.5%</text>
      </g>
      <g>
        <circle cx="851" cy="761" r="59" fill="var(--badge)"/>
        <text class="badge-title" x="851" y="714" text-anchor="middle">WEST END</text>
        <text class="badge-title" x="851" y="723" text-anchor="middle">&amp; MIDTOWN</text>
        <text class="pound" x="851" y="792" text-anchor="middle" fill="var(--crimson)">£</text>
        <text class="badge-pct" x="851" y="812" text-anchor="middle">24.0%</text>
      </g>
    </svg>
  </section>
</main>
</body>
</html>
```